Halvern Studio Works New Business Card

I am opening a new division of my business. I am a high end interior designer, and the new business is writing specs for construction projects. It will be marketed to the VERY high end contractor, architects and realtors. The client will actually be the one who pays us and signs the agreement, but it will be the contractor, architect or realtor that will recommend us. I have attached my current card and our previous logo which is still used on some of our paperwork. I would like the new logo to be connected in some way to what we are currently using. We will need to have room on the card for a person's name. I'd like to omit the address as we might be moving the office soon. The web address is www.HalvernStudioWorks.com. For this design, please use my name, Marisol Thornbury.

Target Market(s)

High End Luxury Contractors, Realtors and Architects

Industry/Entity Type

Residential Construction

Contact Information for Business Card

Halvern Studio Works, Phone: 555-214-9087, www.HalvernStudioWorks.com , Marisol Thornbury

Font styles to use
Sans Serif

Colors
ec1f27

Requirements
Must have
• Some visual reference to my current card and logos. Use the colors submitted on the business card I attached.
Nice to have
• A visual reference to my current card and logos. Use the colors submitted on the card I attached.
Should not have
• A physical address

```html
<!DOCTYPE html>
<html lang="en">
<head>
<meta charset="utf-8">
<title>Halvern Studio Works – Business Card</title>
<link rel="stylesheet" href="https://fonts.googleapis.com/css2?family=Open+Sans:wght@400;700&family=Roboto+Condensed:wght@300&display=swap">
<style>
  :root {
    --backdrop: #e8e5e1;
    --card: #ffffff;
    --brand: #8a3420;
    --brand-text: #7a2315;
    --muted: #6b6b6b;
    --shadow: rgba(0, 0, 0, 0.28);
  }
  * { margin: 0; padding: 0; box-sizing: border-box; }
  html, body { width: 1200px; height: 1000px; overflow: hidden; }
  body { background: var(--backdrop); position: relative; font-family: "Open Sans", Arial, sans-serif; }

  .card {
    position: absolute; left: 265px; width: 665px; height: 397px;
    background: var(--card); box-shadow: 0 3px 10px var(--shadow);
  }
  .card--front { top: 73px; }
  .card--back { top: 533px; }

  .brand-mark { position: absolute; background: var(--brand); }
  .brand-name {
    position: absolute; font-family: "Roboto Condensed", "Arial Narrow", sans-serif;
    font-weight: 300; color: var(--brand-text); white-space: nowrap; text-align: center;
    transform: translateX(-50%);
  }

  .card--front .brand-mark { left: 146px; top: 140px; width: 64px; height: 64px; }
  .card--front .brand-name { left: 178px; top: 214px; font-size: 36px; }

  .contact { position: absolute; left: 365px; top: 132px; }
  .contact__name { font-weight: 700; font-size: 17px; color: var(--brand-text); letter-spacing: 0.2px; margin-bottom: 40px; }
  .contact__list { list-style: none; }
  .contact__item { display: flex; align-items: center; font-size: 15.5px; color: var(--muted); height: 24px; }
  .contact__icon { width: 14px; height: 14px; margin-right: 8px; fill: var(--brand-text); flex: none; }

  .card--back .brand-mark { left: 289px; top: 113px; width: 88px; height: 88px; }
  .card--back .brand-name { left: 333px; top: 216px; font-size: 50px; }
  .tagline { position: absolute; left: 0; right: 0; top: 347px; text-align: center; font-size: 16px; color: var(--muted); }
</style>
</head>
<body>
  <section class="card card--front" aria-label="Business card front">
    <div class="brand-mark"></div>
    <div class="brand-name">Halvern Studio Works</div>

    <div class="contact">
      <p class="contact__name">MARISOL THORNBURY</p>
      <ul class="contact__list">
        <li class="contact__item">
          <svg class="contact__icon" viewBox="0 0 16 16" aria-hidden="true"><path d="M1 5c0-2 3-3 7-3s7 1 7 3v1.5h-3.5V5H4.5v1.5H1zM4 7h8l2 6H2z"/></svg>
          555-214-9087
        </li>
        <li class="contact__item">
          <svg class="contact__icon" viewBox="0 0 16 16" aria-hidden="true"><path d="M1 3h14v10H1zM2.5 4.5 8 9l5.5-4.5"/><path d="M2.5 4.5 8 9l5.5-4.5" fill="none" stroke="#fff" stroke-width="1.2"/></svg>
          info@HalvernStudioWorks.com
        </li>
        <li class="contact__item">
          <svg class="contact__icon" viewBox="0 0 16 16" aria-hidden="true"><path d="M1 2h14v10H1zM2.5 3.5v7h11v-7zM5 13.5h6V15H5z"/></svg>
          www.HalvernStudioWorks.com
        </li>
      </ul>
    </div>
  </section>

  <section class="card card--back" aria-label="Business card back">
    <div class="brand-mark"></div>
    <div class="brand-name">Halvern Studio Works</div>
    <p class="tagline">Commercial &amp; Residential design</p>
  </section>
</body>
</html>
```